1876 Basins & Spouts Business Card

I'm wanting to get a business card designed. Our business is 1876 Basins & Spouts
Details for the card:

1876 Basins & Spouts
Name: Harold Vesk
Email: harold@1876basinsandspouts.com.au
Website: www.1876basinsandspouts.com.au
Mobile: 0438 260 947
Phone: 02 7481 3926

Font of Basins & Spouts is called Snell Roundhand. Not sue what font logo text is.

I'm thinking two sided but it doesn't have to be.

```html
<!DOCTYPE html>
<html lang="en">
<head>
<meta charset="utf-8">
<title>1876 Basins &amp; Spouts – Business Card</title>
<link rel="stylesheet" href="https://fonts.googleapis.com/css2?family=Pinyon+Script&family=Open+Sans:wght@400;600&display=swap">
<style>
  :root {
    --backdrop: #1b1b1b;
    --card: #0f0f10;
    --card-edge: #232325;
    --ink: #ffffff;
    --ink-soft: #c9c9c9;
    --rule: #3a3a3c;
  }
  * { box-sizing: border-box; margin: 0; padding: 0; }
  html, body {
    width: 1200px; height: 900px; overflow: hidden;
    background: var(--backdrop);
  }
  .canvas { position: relative; width: 1200px; height: 900px; }
  .card {
    position: absolute; left: 290px;
    width: 620px; height: 354px;
    background: var(--card);
    border: 1px solid var(--card-edge);
    border-radius: 22px;
    box-shadow: 0 14px 36px rgba(0,0,0,.55);
    color: var(--ink);
    overflow: hidden;
  }
  .card--front { top: 70px; }
  .card--back { top: 476px; }

  .script { font-family: "Pinyon Script", cursive; font-weight: 400; }
  .sans { font-family: "Open Sans", sans-serif; }

  /* front */
  .front-wordmark {
    position: absolute; left: 0; right: 0; top: 120px;
    text-align: center; font-size: 64px; line-height: 1;
  }
  .front-web {
    position: absolute; right: 92px; bottom: 64px;
    font-size: 15px; font-weight: 600; letter-spacing: .2px;
  }

  /* back */
  .brand {
    position: absolute; left: 40px; right: 40px; top: 62px;
    text-align: right;
  }
  .brand-name {
    font-size: 28px; font-weight: 400; line-height: 1.1;
    color: var(--ink); letter-spacing: .5px;
  }
  .brand-tagline {
    font-size: 11px; color: var(--ink-soft); margin-top: 8px; letter-spacing: .2px;
  }
  .brand-rule {
    position: absolute; left: 340px; right: 40px; top: 150px;
    height: 1px; background: var(--rule);
  }
  .contact-links {
    position: absolute; right: 40px; top: 170px;
    text-align: right; font-size: 15px; line-height: 22px; color: var(--ink-soft);
  }
  .contact-links li, .phones li { list-style: none; display: flex; align-items: center; gap: 8px; }
  .contact-links li { justify-content: flex-end; }
  .icon { width: 14px; height: 14px; flex: none; fill: var(--ink); }
  .person {
    position: absolute; left: 40px; top: 238px;
    font-size: 36px; line-height: 1;
  }
  .person-rule {
    position: absolute; left: 228px; right: 300px; top: 262px;
    height: 1px; background: var(--rule);
  }
  .phones {
    position: absolute; left: 40px; top: 284px;
    font-size: 17px; line-height: 24px; color: var(--ink-soft);
  }
</style>
</head>
<body>
<main class="canvas">

  <section class="card card--front" aria-label="Card front">
    <h1 class="front-wordmark script">Basins &amp; Spouts</h1>
    <p class="front-web sans">www.1876basinsandspouts.com.au</p>
  </section>

  <section class="card card--back" aria-label="Card back">
    <div class="brand">
      <p class="brand-name sans">1876 Basins &amp; Spouts</p>
      <p class="brand-tagline sans">Classic fittings crafted for the way you live today</p>
    </div>
    <div class="brand-rule"></div>

    <ul class="contact-links sans">
      <li>harold@1876basinsandspouts.com.au
        <svg class="icon" viewBox="0 0 16 16" aria-hidden="true"><path d="M1 3h14v10H1z" fill="none" stroke="#fff" stroke-width="1.5"/><path d="M1 3l7 6 7-6" fill="none" stroke="#fff" stroke-width="1.5"/></svg>
      </li>
      <li>www.1876basinsandspouts.com.au
        <svg class="icon" viewBox="0 0 16 16" aria-hidden="true"><circle cx="8" cy="8" r="6.5" fill="none" stroke="#fff" stroke-width="1.5"/><path d="M1.5 8h13M8 1.5c3 3.5 3 9.5 0 13M8 1.5c-3 3.5-3 9.5 0 13" fill="none" stroke="#fff" stroke-width="1.2"/></svg>
      </li>
    </ul>

    <p class="person script">Harold Vesk</p>
    <div class="person-rule"></div>

    <ul class="phones sans">
      <li>
        <svg class="icon" viewBox="0 0 16 16" aria-hidden="true"><path d="M4 2l2.5 3-1.5 1.5c.8 1.8 2.2 3.2 4 4L10.5 9 13.5 11.5 12 14C6.5 13.5 2.5 9.5 2 4z"/></svg>
        0438 260 947
      </li>
      <li>
        <svg class="icon" viewBox="0 0 16 16" aria-hidden="true"><rect x="4" y="1" width="8" height="14" rx="1.5" fill="none" stroke="#fff" stroke-width="1.5"/><circle cx="8" cy="12.5" r=".9"/></svg>
        02 7481 3926
      </li>
    </ul>
  </section>

</main>
</body>
</html>
```